Software Development Consulting Company Needs Business Card Design

We need a new business card design for our consultants at Kestrel Works (kestrelworks.example). We are a small firm that provides high-end software development and methodology consulting to medium to large enterprise IT organizations.

Our logo uses Futura for the font and we would like to stick with navy blue and canary yellow for the logo colors. Attached are normal and reversed versions of our logos in illustrator format.
Updates

Hi Everyone, Thank yo very much for your amazing design ideas. I have created a poll for this project and our employees will be voting on the design they wish to use. We will be making a decision this Wednesday (October 22nd). Thanks again, Dale Hartwick

Industry/Entity Type

Business

```html
<!DOCTYPE html>
<html lang="en">
<head>
<meta charset="utf-8">
<title>Kestrel Works – Business Card</title>
<link href="https://fonts.googleapis.com/css2?family=PT+Sans:wght@400;700&display=swap" rel="stylesheet">
<style>
  :root {
    --navy: #1d4a6e;
    --canary: #f2e300;
    --white: #ffffff;
    --ink: #333a40;
    --page: #e9eaee;
    --rule: #b9bcc0;
  }
  * { margin: 0; padding: 0; box-sizing: border-box; }
  html, body {
    width: 1200px; height: 980px; overflow: hidden;
    background: var(--page);
    font-family: "PT Sans", Arial, sans-serif;
  }
  .sheet {
    width: 1200px; height: 980px;
    display: flex; flex-direction: column; align-items: center; justify-content: center;
    gap: 44px;
  }
  .card {
    position: relative;
    width: 760px; height: 434px;
    border-radius: 30px;
    overflow: hidden;
    box-shadow: 0 6px 18px rgba(0,0,0,0.12);
  }

  /* Back */
  .card-back { background: var(--navy); color: var(--white); }
  .card-back .brand {
    position: absolute; left: 0; right: 0; top: 150px;
    display: flex; align-items: center; justify-content: center; gap: 16px;
    font-size: 46px; font-weight: 700; letter-spacing: 6px; text-transform: uppercase;
  }
  .card-back .brand-dot {
    width: 22px; height: 22px; border-radius: 50%; background: var(--canary);
  }
  .card-back .web {
    position: absolute; left: 0; right: 0; top: 280px;
    text-align: center; font-size: 22px; letter-spacing: 5px;
  }

  /* Front */
  .card-front { background: var(--white); }
  .card-front .swoosh { position: absolute; inset: 0; }
  .card-front .brand {
    position: absolute; left: 48px; top: 82px;
    display: flex; align-items: center; gap: 12px;
    color: var(--navy); font-size: 40px; font-weight: 700; letter-spacing: 5px; text-transform: uppercase;
  }
  .card-front .brand-dot {
    width: 14px; height: 14px; border-radius: 50%; background: var(--canary);
  }
  .card-front .divider {
    position: absolute; left: 420px; top: 60px; width: 2px; height: 170px;
    background: linear-gradient(to bottom, transparent, var(--rule) 40%, var(--rule) 60%, transparent);
  }
  .contact {
    position: absolute; left: 450px; top: 74px;
    list-style: none; color: var(--ink); font-size: 19px; line-height: 32px;
  }
  .contact li { display: flex; align-items: center; gap: 9px; }
  .contact svg { width: 18px; height: 18px; flex: none; }
  .contact .place { padding-left: 0; }
  .holder {
    position: absolute; right: 46px; bottom: 26px;
    color: var(--white); font-size: 30px; font-weight: 700;
  }
  .holder .title { font-size: 22px; font-weight: 400; }
</style>
</head>
<body>
<main class="sheet">

  <section class="card card-back">
    <div class="brand"><span>Kestrel Works</span><span class="brand-dot"></span></div>
    <div class="web">www.kestrelworks.example</div>
  </section>

  <section class="card card-front">
    <svg class="swoosh" viewBox="0 0 760 434" preserveAspectRatio="none">
      <path d="M0,150 C140,262 330,344 760,352 L760,434 L0,434 Z" fill="var(--navy)"/>
      <path d="M0,138 C140,250 330,332 760,340" fill="none" stroke="var(--canary)" stroke-width="5"/>
    </svg>

    <div class="brand"><span>Kestrel Works</span><span class="brand-dot"></span></div>
    <div class="divider"></div>

    <ul class="contact">
      <li>
        <svg viewBox="0 0 20 20"><circle cx="10" cy="10" r="9" fill="var(--navy)"/><path d="M7 5.5 L8.8 5.5 L9.5 8 L8.4 8.9 C9 10.3 9.9 11.2 11.2 11.8 L12.1 10.7 L14.5 11.4 L14.5 13.2 C10 13.6 6.6 10 7 5.5 Z" fill="var(--white)"/></svg>
        555-014-2738
      </li>
      <li>
        <svg viewBox="0 0 20 20"><rect x="1.5" y="4" width="17" height="12" rx="1.5" fill="var(--navy)"/><path d="M2.5 5 L10 11 L17.5 5" fill="none" stroke="var(--white)" stroke-width="1.4"/></svg>
        info@kestrelworks.example
      </li>
      <li>
        <svg viewBox="0 0 20 20"><circle cx="10" cy="10" r="8.5" fill="var(--navy)"/><g fill="none" stroke="var(--white)" stroke-width="1"><ellipse cx="10" cy="10" rx="3.6" ry="8.5"/><path d="M1.5 10 H18.5 M3 6 H17 M3 14 H17"/></g></svg>
        www.kestrelworks.example
      </li>
      <li class="place">Riverton + Oakdale, IL</li>
    </ul>

    <p class="holder">Your Name, <span class="title">Title</span></p>
  </section>

</main>
</body>
</html>
```